Dorin Velk Personal Card

I am looking for a personal card that has my contact information on the front and then the url for my website on the back. I am a fan of minimal, modern design, but am very open minded to other styles. Both portrait and landscape designs are acceptable. The only other specification that I have is that some sort of graphic of a raven is present somewhere on the card (my last name 'Velk' means raven in German).
Industry/Entity Type
Landscape
Contact Information for Business Card
Dorin Velk
608.514.2936
dorinpvelk@postquill.net
dorinpvelk.com
Colors
Requirements
Must have
- Raven on some part of the card

```html
<!DOCTYPE html>
<html lang="en">
<head>
<meta charset="utf-8">
<title>Dorin Velk Personal Card</title>
<link href="https://fonts.googleapis.com/css2?family=Open+Sans:wght@400;600&display=swap" rel="stylesheet">
<style>
  :root {
    --backdrop: #4a413b;
    --card: #141414;
    --card-edge: #1d1d1d;
    --foil: #c9c9c9;
    --foil-dim: #9a9a9a;
    --spot-dark: #0b0b0b;
    --raven-light: #d8d8d8;
    --url-ink: #3a3a3a;
  }
  * { box-sizing: border-box; margin: 0; padding: 0; }
  html, body { width: 1200px; height: 847px; overflow: hidden; }
  body {
    background: var(--backdrop);
    font-family: "Open Sans", Arial, sans-serif;
    position: relative;
  }
  .card {
    position: absolute;
    top: 276px;
    width: 520px;
    height: 296px;
    background: var(--card);
    border: 1px solid var(--card-edge);
    border-radius: 6px;
    box-shadow: 0 14px 30px rgba(0,0,0,0.45);
  }
  .card--back { left: 50px; }
  .card--front { left: 630px; }

  .raven-art {
    position: absolute;
    left: 200px;
    top: 34px;
    width: 240px;
    height: 190px;
    border-radius: 50% 45% 40% 50%;
    background: linear-gradient(160deg, var(--spot-dark) 0%, #2a2a2a 45%, var(--raven-light) 100%);
  }
  .site-url {
    position: absolute;
    left: 150px;
    top: 236px;
    font-size: 17px;
    color: var(--url-ink);
    letter-spacing: 0.3px;
  }

  .contact {
    position: absolute;
    left: 250px;
    top: 104px;
  }
  .contact__name {
    font-weight: 600;
    font-size: 27px;
    color: var(--foil);
    margin-left: 14px;
    margin-bottom: 6px;
  }
  .contact__list { list-style: none; }
  .contact__item {
    display: flex;
    align-items: center;
    gap: 10px;
    font-size: 13px;
    color: var(--foil-dim);
    height: 22px;
  }
  .contact__item--phone { padding-left: 14px; }
  .contact__icon { width: 12px; height: 12px; flex: none; }
</style>
</head>
<body>
  <section class="card card--back" aria-label="Card back">
    <div class="raven-art" role="img" aria-label="Raven in flight, spot-gloss illustration"></div>
    <p class="site-url">www.dorinpvelk.com</p>
  </section>

  <section class="card card--front" aria-label="Card front">
    <div class="contact">
      <h1 class="contact__name">Dorin Velk</h1>
      <ul class="contact__list">
        <li class="contact__item contact__item--phone">
          <svg class="contact__icon" viewBox="0 0 12 12" aria-hidden="true"><rect x="3" y="0.5" width="6" height="11" rx="1" fill="none" stroke="#9a9a9a"/></svg>
          608.514.2936
        </li>
        <li class="contact__item">
          <svg class="contact__icon" viewBox="0 0 12 12" aria-hidden="true"><rect x="0.5" y="2" width="11" height="8" fill="#9a9a9a"/><path d="M0.5 2 L6 7 L11.5 2" fill="none" stroke="#141414"/></svg>
          dorinpvelk@postquill.net
        </li>
        <li class="contact__item">
          <svg class="contact__icon" viewBox="0 0 12 12" aria-hidden="true"><circle cx="6" cy="6" r="5.5" fill="#9a9a9a"/><path d="M0.5 6 H11.5 M6 0.5 V11.5" stroke="#141414"/><ellipse cx="6" cy="6" rx="2.5" ry="5.5" fill="none" stroke="#141414"/></svg>
          www.dorinpvelk.com
        </li>
      </ul>
    </div>
  </section>
</body>
</html>
```